Business Card Design Project

Business card based on attached logo

Todd Merrick
Todd@lorvantest.com
877-514-9073 ext. 318
Www.LorvanTest.com

Industry/Entity Type

Business

```html
<!DOCTYPE html>
<html lang="en">
<head>
<meta charset="utf-8">
<title>LorvanTest Business Cards</title>
<link rel="stylesheet" href="https://fonts.googleapis.com/css2?family=Arimo:wght@400;700&display=swap">
<style>
  :root {
    --backdrop: #8a8c8f;
    --paper: #ffffff;
    --ink: #231f20;
    --brand-red: #e3262c;
    --brand-red-deep: #b81e24;
    --charcoal: #2b2b2b;
    --charcoal-deep: #161616;
    --tint-pink: #fbe3e4;
  }
  * { box-sizing: border-box; margin: 0; padding: 0; }
  html, body {
    width: 1200px; height: 720px; overflow: hidden;
    background: var(--backdrop);
    font-family: "Arimo", Arial, sans-serif;
  }
  .sheet { position: relative; width: 1200px; height: 720px; }
  .card {
    position: absolute; width: 564px; height: 322px; overflow: hidden;
    box-shadow: 0 0 0 1px rgba(0,0,0,0.12);
  }
  .card--front { left: 26px; top: 26px; background: var(--paper); }
  .card--red { left: 612px; top: 26px; background: linear-gradient(135deg, var(--brand-red) 0%, var(--brand-red-deep) 100%); }
  .card--white { left: 26px; top: 373px; background: var(--paper); }
  .card--dark { left: 612px; top: 373px; background: radial-gradient(ellipse at 50% 40%, #3a3a3a 0%, var(--charcoal) 45%, var(--charcoal-deep) 100%); }

  .corner-curl { position: absolute; left: 0; top: 0; width: 564px; height: 322px; }

  .holder-name {
    position: absolute; right: 30px; top: 26px;
    color: var(--paper); font-size: 19px; font-weight: 400; letter-spacing: 0.3px;
  }

  .wordmark {
    position: absolute; display: flex; align-items: center; gap: 12px;
    font-weight: 700; letter-spacing: -1px; line-height: 1;
  }
  .wordmark__dot { display: block; flex: none; }
  .wordmark--front { left: 30px; top: 92px; font-size: 52px; color: var(--ink); }
  .wordmark--front .wordmark__dot { width: 22px; height: 22px; background: var(--brand-red); }
  .wordmark--red { left: 34px; top: 70px; font-size: 80px; color: var(--paper); }
  .wordmark--white, .wordmark--dark {
    left: 0; right: 0; top: 122px; justify-content: center; font-size: 66px;
  }
  .wordmark--white { color: var(--ink); }
  .wordmark--white .wordmark__dot { width: 26px; height: 26px; background: var(--brand-red); }
  .wordmark--dark { color: var(--paper); }
  .wordmark--dark .wordmark__dot { width: 26px; height: 26px; background: var(--paper); }

  .contact-list { position: absolute; left: 34px; top: 226px; list-style: none; }
  .contact-list li {
    display: flex; align-items: center; gap: 8px; height: 27.5px;
    font-size: 17px; color: var(--ink);
  }
  .contact-list svg { width: 13px; height: 13px; flex: none; }

  .faint-square { position: absolute; }
  .faint-square--front { left: 461px; top: 222px; width: 88px; height: 88px; background: var(--tint-pink); }
  .faint-square--red { left: 394px; top: 152px; width: 170px; height: 110px; background: rgba(255,255,255,0.14); box-shadow: 0 0 3px rgba(0,0,0,0.15); }

  .web-address { position: absolute; font-size: 17px; letter-spacing: 3px; }
  .web-address--red { left: 36px; bottom: 16px; color: var(--paper); }
  .web-address--white, .web-address--dark { left: 0; right: 0; bottom: 26px; text-align: center; }
  .web-address--white { color: var(--ink); }
  .web-address--dark { color: var(--paper); }
</style>
</head>
<body>
<main class="sheet">

  <section class="card card--front" aria-label="Card front with contact details">
    <div class="faint-square faint-square--front"></div>
    <svg class="corner-curl" viewBox="0 0 564 322" aria-hidden="true">
      <defs>
        <linearGradient id="cornerRed" x1="0" y1="0" x2="1" y2="1">
          <stop offset="0" stop-color="#e3262c"/>
          <stop offset="1" stop-color="#a81b20"/>
        </linearGradient>
        <linearGradient id="curlShade" x1="0" y1="0" x2="1" y2="1">
          <stop offset="0" stop-color="#4a4a4a"/>
          <stop offset="0.6" stop-color="#1e1e1e"/>
          <stop offset="1" stop-color="#000"/>
        </linearGradient>
      </defs>
      <polygon points="262,0 564,0 564,118" fill="url(#cornerRed)"/>
      <path d="M262 0 L564 118 L564 128 C546 138 536 170 542 206 C470 150 360 70 262 0 Z" fill="url(#curlShade)"/>
    </svg>
    <p class="holder-name">TODD MERRICK</p>
    <div class="wordmark wordmark--front">
      <span>LorvanTest</span><span class="wordmark__dot"></span>
    </div>
    <ul class="contact-list">
      <li>
        <svg viewBox="0 0 14 14" aria-hidden="true"><circle cx="7" cy="7" r="6.3" fill="none" stroke="#e3262c" stroke-width="1.4"/><path d="M4.5 3.5 L6 5.5 L5.2 6.4 C5.8 7.6 6.6 8.4 7.6 9 L8.5 8.1 L10.5 9.5 L9.6 10.7 C7 10.4 3.8 7.2 3.4 4.4 Z" fill="#e3262c"/></svg>
        <span>877-514-9073 ext. 318</span>
      </li>
      <li>
        <svg viewBox="0 0 14 14" aria-hidden="true"><rect x="1" y="3" width="12" height="9" fill="#e3262c"/><path d="M1 3 L7 8 L13 3" fill="none" stroke="#fff" stroke-width="1.2"/></svg>
        <span>Todd@lorvantest.com</span>
      </li>
      <li>
        <svg viewBox="0 0 14 14" aria-hidden="true"><circle cx="7" cy="7" r="6" fill="none" stroke="#e3262c" stroke-width="1.3"/><ellipse cx="7" cy="7" rx="2.6" ry="6" fill="none" stroke="#e3262c" stroke-width="1"/><line x1="1" y1="7" x2="13" y2="7" stroke="#e3262c" stroke-width="1"/></svg>
        <span>www.lorvantest.com</span>
      </li>
    </ul>
  </section>

  <section class="card card--red" aria-label="Red card back">
    <div class="faint-square faint-square--red"></div>
    <div class="wordmark wordmark--red"><span>LorvanTest</span></div>
    <p class="web-address web-address--red">www.lorvantest.com</p>
  </section>

  <section class="card card--white" aria-label="White card back">
    <div class="wordmark wordmark--white">
      <span>LorvanTest</span><span class="wordmark__dot"></span>
    </div>
    <p class="web-address web-address--white">www.lorvantest.com</p>
  </section>

  <section class="card card--dark" aria-label="Dark card back">
    <div class="wordmark wordmark--dark">
      <span>LorvanTest</span><span class="wordmark__dot"></span>
    </div>
    <p class="web-address web-address--dark">www.lorvantest.com</p>
  </section>

</main>
</body>
</html>
```